Accounting firm needing business card / letterhead designed
Marcus L. Trenholm, CPA
marcus@veltrowledger.com
www.veltrowledger.com
842 E Alder Ave Marlow Bend, IA 43827
555-562-0974

```html
<!DOCTYPE html>
<html lang="en">
<head>
<meta charset="utf-8">
<title>Veltrow Ledger – Business Card</title>
<link href="https://fonts.googleapis.com/css2?family=Roboto:wght@400;500&family=Roboto+Condensed:wght@700&display=swap" rel="stylesheet">
<style>
  :root {
    --navy: #231f5c;
    --green: #86bd3a;
    --paper: #f7f7f7;
    --ink-grey: #4a4a4a;
    --rule: #9a9a9a;
    --backdrop: #e2e2e2;
    --white: #ffffff;
  }
  html, body {
    margin: 0;
    padding: 0;
    width: 1200px;
    height: 960px;
    overflow: hidden;
    background: var(--backdrop);
  }
  .canvas {
    position: relative;
    width: 1200px;
    height: 960px;
  }
  .card {
    position: absolute;
    overflow: hidden;
  }
  .card-front {
    left: 314px;
    top: 113px;
    width: 602px;
    height: 342px;
    background: var(--paper);
  }
  .card-back {
    left: 311px;
    top: 472px;
    width: 600px;
    height: 343px;
    background: var(--navy);
  }
  .brand-name {
    position: absolute;
    font-family: "Roboto", sans-serif;
    font-weight: 500;
    letter-spacing: 3px;
    white-space: nowrap;
    margin: 0;
  }
  .card-front .brand-name {
    right: 36px;
    top: 48px;
    font-size: 36px;
    color: var(--navy);
  }
  .card-back .brand-name {
    left: 0;
    right: 0;
    top: 146px;
    text-align: center;
    font-size: 44px;
    color: var(--white);
  }
  .person-name {
    position: absolute;
    left: 34px;
    top: 206px;
    margin: 0;
    font-family: "Roboto Condensed", sans-serif;
    font-weight: 700;
    font-size: 21px;
    color: var(--navy);
  }
  .divider {
    position: absolute;
    left: 34px;
    top: 240px;
    width: 531px;
    height: 1px;
    background: var(--rule);
  }
  .contact-list {
    position: absolute;
    left: 34px;
    top: 253px;
    margin: 0;
    padding: 0;
    list-style: none;
    font-family: "Roboto", sans-serif;
    font-size: 14.5px;
    color: var(--ink-grey);
    line-height: 20px;
  }
  .contact-list li {
    display: flex;
    align-items: center;
    gap: 8px;
  }
  .contact-list svg {
    width: 13px;
    height: 13px;
  }
  .address {
    position: absolute;
    right: 35px;
    top: 255px;
    margin: 0;
    font-style: normal;
    text-align: right;
    font-family: "Roboto", sans-serif;
    font-size: 14.5px;
    line-height: 20px;
    color: var(--ink-grey);
  }
  .footer-band {
    position: absolute;
    left: 0;
    bottom: 0;
    width: 602px;
    height: 34px;
  }
  .footer-url {
    position: absolute;
    right: 32px;
    bottom: 11px;
    margin: 0;
    font-family: "Roboto", sans-serif;
    font-size: 14px;
    letter-spacing: 1px;
    color: var(--white);
  }
  .back-url {
    position: absolute;
    left: 0;
    right: 0;
    top: 282px;
    margin: 0;
    text-align: center;
    font-family: "Roboto", sans-serif;
    font-size: 14px;
    letter-spacing: 6px;
    color: var(--white);
  }
</style>
</head>
<body>
<main class="canvas">
  <section class="card card-front">
    <p class="brand-name">VELTROW LEDGER</p>
    <h1 class="person-name">Marcus L. Trenholm, CPA</h1>
    <div class="divider"></div>
    <ul class="contact-list">
      <li>
        <svg viewBox="0 0 24 24" aria-hidden="true"><path fill="var(--navy)" d="M6.6 10.8a15.1 15.1 0 0 0 6.6 6.6l2.2-2.2a1 1 0 0 1 1-.25 11.4 11.4 0 0 0 3.6.57 1 1 0 0 1 1 1V20a1 1 0 0 1-1 1A17 17 0 0 1 3 4a1 1 0 0 1 1-1h3.5a1 1 0 0 1 1 1 11.4 11.4 0 0 0 .57 3.6 1 1 0 0 1-.25 1z"/></svg>
        <span>555-562-0974</span>
      </li>
      <li>
        <svg viewBox="0 0 24 24" aria-hidden="true"><rect x="2" y="5" width="20" height="14" fill="var(--navy)"/><polyline points="2,6 12,13 22,6" fill="none" stroke="var(--paper)" stroke-width="2"/></svg>
        <span>marcus@veltrowledger.com</span>
      </li>
    </ul>
    <address class="address">842 E Alder Ave<br>Marlow Bend, IA 43827</address>
    <svg class="footer-band" viewBox="0 0 602 34" aria-hidden="true">
      <rect x="0" y="13" width="350" height="8" fill="var(--green)"/>
      <rect x="0" y="21" width="602" height="13" fill="var(--navy)"/>
      <polygon points="342,34 364,0 602,0 602,34" fill="var(--navy)"/>
    </svg>
    <p class="footer-url">www.veltrowledger.com</p>
  </section>

  <section class="card card-back">
    <p class="brand-name">VELTROW LEDGER</p>
    <p class="back-url">www.veltrowledger.com</p>
  </section>
</main>
</body>
</html>
```